Business Card for Professional Photographer

I'm looking for an eye catching modern clean design that compliments my logo/ website fonts & colours.
I specialise in architecture, corporate & commercial photography so I'm marketing to professional clients rather than portrait / wedding clients.

I would prefer to not have a solid black design.

My logo brand guide is as follows :

Main front font. : Reislust
Main font colour : #fff
Slogan front font : Ubuntu Bold
Monogram front font : Venti Medium
Container colour : #fff

I need print ready files in pdf .png & .eps formats.

Included in the files below are some screen grabs as reference to font & colours etc.

```html
<!DOCTYPE html>
<html lang="en">
<head>
<meta charset="utf-8">
<title>Keel Light – Business Card</title>
<link rel="stylesheet" href="https://fonts.googleapis.com/css2?family=Montserrat:wght@300&family=Roboto:wght@400&family=Ubuntu:wght@400;700&display=swap">
<style>
  :root {
    --backdrop: #3b3b3d;
    --card-black: #1d1d1f;
    --gold: #c9a24a;
    --gold-light: #f1dc97;
    --gold-deep: #a9822f;
    --silver: #b9b9bb;
    --white: #ffffff;
    --ink: #111111;
  }
  * { margin: 0; padding: 0; box-sizing: border-box; }
  html, body { width: 799px; height: 1200px; overflow: hidden; }
  body {
    background: var(--backdrop);
    position: relative;
    font-family: "Roboto", sans-serif;
  }
  .card {
    position: absolute;
    left: 60px;
    width: 680px;
    height: 390px;
    background: var(--card-black);
    border-radius: 4px;
    overflow: hidden;
  }
  .card--front { top: 130px; }
  .card--back { top: 690px; }

  /* Front */
  .front-mark {
    position: absolute;
    top: 140px;
    left: 0;
    width: 100%;
    text-align: center;
    font-family: "Montserrat", sans-serif;
    font-weight: 300;
    font-size: 46px;
    letter-spacing: 10px;
    color: var(--silver);
  }
  .front-url {
    position: absolute;
    top: 300px;
    left: 0;
    width: 100%;
    text-align: center;
    font-family: "Ubuntu", sans-serif;
    font-size: 15px;
    letter-spacing: 2.5px;
    color: var(--gold);
  }

  /* Back */
  .brand {
    position: absolute;
    top: 40px;
    left: 44px;
    display: flex;
    align-items: center;
    gap: 14px;
  }
  .brand__square {
    width: 18px;
    height: 18px;
    background: var(--gold);
  }
  .brand__name {
    font-family: "Montserrat", sans-serif;
    font-weight: 300;
    font-size: 34px;
    letter-spacing: 6px;
    color: var(--gold);
  }
  .tagline {
    position: absolute;
    top: 88px;
    left: 78px;
    font-family: "Ubuntu", sans-serif;
    font-weight: 700;
    font-size: 12px;
    letter-spacing: 3px;
    color: var(--gold-deep);
  }
  .contact {
    position: absolute;
    top: 122px;
    left: 44px;
    list-style: none;
    color: var(--white);
    font-size: 15px;
    line-height: 20px;
  }
  .contact li { display: flex; align-items: center; gap: 10px; }
  .contact__icon { width: 12px; height: 12px; flex: none; }
  .contact__address { padding-left: 22px; }
  .wave { position: absolute; left: 0; top: 0; width: 680px; height: 390px; }
  .person {
    position: absolute;
    right: 70px;
    bottom: 50px;
    text-align: right;
    color: var(--ink);
    font-family: "Ubuntu", sans-serif;
  }
  .person__name { font-weight: 700; font-size: 23px; }
  .person__role { font-size: 17px; }
</style>
</head>
<body>
  <section class="card card--front">
    <div class="front-mark">KEEL LIGHT</div>
    <div class="front-url">www.keellight.com.au</div>
  </section>

  <section class="card card--back">
    <svg class="wave" viewBox="0 0 680 390" aria-hidden="true">
      <defs>
        <linearGradient id="goldFill" x1="0" y1="0" x2="1" y2="1">
          <stop offset="0" stop-color="#b8913c"/>
          <stop offset="0.5" stop-color="#e9cf85"/>
          <stop offset="1" stop-color="#f6e6a6"/>
        </linearGradient>
        <linearGradient id="goldBand" x1="0" y1="0" x2="1" y2="0">
          <stop offset="0" stop-color="#d8b661"/>
          <stop offset="1" stop-color="#9c7628"/>
        </linearGradient>
      </defs>
      <path d="M0,205 C150,200 270,280 440,268 C560,258 630,215 680,195 L680,212 C620,240 550,280 440,288 C270,300 140,225 0,222 Z" fill="url(#goldBand)"/>
      <path d="M0,240 C140,236 270,322 440,305 C560,292 630,252 680,232 L680,390 L0,390 Z" fill="url(#goldFill)"/>
    </svg>

    <div class="brand">
      <span class="brand__square"></span>
      <span class="brand__name">KEEL LIGHT</span>
    </div>
    <div class="tagline">Architecture Corporate commercial</div>

    <ul class="contact">
      <li class="contact__address">48 Harbour Ln Brightwater Vic 3199</li>
      <li>
        <svg class="contact__icon" viewBox="0 0 12 12"><path d="M2,1 L4,1 L5,4 L3.5,5 C4.3,6.8 5.2,7.7 7,8.5 L8,7 L11,8 L11,10 C11,10.6 10.6,11 10,11 C5,11 1,7 1,2 C1,1.4 1.4,1 2,1 Z" fill="#c9a24a"/></svg>
        0412556781
      </li>
      <li>
        <svg class="contact__icon" viewBox="0 0 12 12"><rect x="0.5" y="2" width="11" height="8" fill="#c9a24a"/><path d="M0.5,2 L6,6.5 L11.5,2" fill="none" stroke="#1d1d1f" stroke-width="1"/></svg>
        hello@keellight.com.au
      </li>
      <li>
        <svg class="contact__icon" viewBox="0 0 12 12"><circle cx="6" cy="6" r="5.5" fill="#c9a24a"/><path d="M0.5,6 H11.5 M6,0.5 V11.5" stroke="#1d1d1f" stroke-width="0.8"/><ellipse cx="6" cy="6" rx="2.4" ry="5.5" fill="none" stroke="#1d1d1f" stroke-width="0.8"/></svg>
        www.keellight.com.au
      </li>
    </ul>

    <div class="person">
      <div class="person__name">Marcus Hale</div>
      <div class="person__role">Photographer</div>
    </div>
  </section>
</body>
</html>
```